Satchel & Sundial needs new business card design

I need a new business card design. I'm looking for out-of-the-box design which represents the freedom of being a location independent entrepreneur.
I offer coaching, retreats and trips.
I would like to see designs with and without the photo.
Colors I use are black (#000000), green (#25A796) and brown (#D7C38C)
Website satchelandsundial.example

Target Market(s)

location independent entrepreneurs, digital nomads, people looking to swap the 9 to 5 for a lifestyle business

Industry/Entity Type

Business

Contact Information for Business Card

Dorota Falkner
Your Lifestyle Business Coach, Retreat & Trip Leader
http://satchelandsundial.example
hello@satchelandsundial.example
Live a life you don't need a holiday from

Font styles to use
Serif
Sans Serif

Requirements
Must have
• One side should contain only the logo. I would also consider having the "Live a life you don't need a holiday from" on that side too (depending on how it looks)
• Please show both sides on the designs.

```html
<!DOCTYPE html>
<html lang="en">
<head>
<meta charset="utf-8">
<title>Satchel &amp; Sundial – Business Card</title>
<link rel="stylesheet" href="https://fonts.googleapis.com/css2?family=Open+Sans:wght@400;600;700&display=swap">
<style>
  :root {
    --ink: #000000;
    --teal: #25A796;
    --kraft-light: #CDAE84;
    --kraft: #C3A275;
    --kraft-dark: #B8966A;
    --page: #FFFFFF;
  }
  html, body {
    margin: 0;
    padding: 0;
    width: 1200px;
    height: 900px;
    overflow: hidden;
    background: var(--page);
    font-family: "Open Sans", Arial, sans-serif;
    color: var(--ink);
  }
  .canvas {
    position: relative;
    width: 1200px;
    height: 900px;
  }
  .card {
    position: absolute;
    background: linear-gradient(135deg, var(--kraft-light), var(--kraft) 55%, var(--kraft-dark));
  }
  .card--front {
    left: 237px;
    top: 42px;
    width: 598px;
    height: 370px;
    clip-path: polygon(0 0, 490px 0, 598px 112px, 598px 258px, 486px 370px, 0 370px);
  }
  .card--back {
    left: 460px;
    top: 515px;
    width: 560px;
    height: 347px;
    clip-path: polygon(108px 0, 560px 0, 560px 347px, 108px 347px, 0 236px, 0 110px);
  }
  .holder-name {
    position: absolute;
    left: 43px;
    top: 48px;
    margin: 0;
    font-size: 19px;
    font-weight: 700;
  }
  .holder-role {
    position: absolute;
    left: 43px;
    top: 73px;
    margin: 0;
    font-size: 15px;
    line-height: 24px;
  }
  .brand-name {
    position: absolute;
    margin: 0;
    font-weight: 700;
    color: var(--ink);
    white-space: nowrap;
  }
  .card--front .brand-name {
    right: 50px;
    top: 172px;
    font-size: 34px;
  }
  .card--back .brand-name {
    right: 58px;
    top: 640px;
    top: 125px;
    font-size: 42px;
  }
  .contact-list {
    position: absolute;
    left: 44px;
    top: 230px;
    margin: 0;
    padding: 0;
    list-style: none;
    font-size: 15px;
    line-height: 23px;
  }
  .contact-list li {
    display: flex;
    align-items: center;
    gap: 10px;
  }
  .contact-icon {
    width: 11px;
    height: 11px;
  }
  .tagline {
    position: absolute;
    left: 46px;
    top: 298px;
    margin: 0;
    font-size: 22px;
  }
</style>
</head>
<body>
<main class="canvas">
  <section class="card card--front" aria-label="Business card front">
    <h1 class="holder-name">Dorota Falkner</h1>
    <p class="holder-role">Your Lifestyle Business Coach,<br>Retreat &amp; Trip Leader</p>
    <p class="brand-name">Satchel &amp; Sundial</p>
    <ul class="contact-list">
      <li>
        <svg class="contact-icon" viewBox="0 0 12 12" aria-hidden="true">
          <rect x="0.5" y="2" width="11" height="8" fill="var(--ink)"/>
          <polyline points="0.5,2.5 6,6.5 11.5,2.5" fill="none" stroke="var(--kraft)" stroke-width="1"/>
        </svg>
        hello@satchelandsundial.example
      </li>
      <li>
        <svg class="contact-icon" viewBox="0 0 12 12" aria-hidden="true">
          <circle cx="6" cy="6" r="5.5" fill="var(--ink)"/>
          <path d="M1 6 H11 M6 0.5 C3 3 3 9 6 11.5 M6 0.5 C9 3 9 9 6 11.5" fill="none" stroke="var(--kraft)" stroke-width="0.8"/>
        </svg>
        www.satchelandsundial.example
      </li>
    </ul>
    <p class="tagline">Live a life you don't need a holiday from</p>
  </section>

  <section class="card card--back" aria-label="Business card back">
    <p class="brand-name">Satchel &amp; Sundial</p>
  </section>
</main>
</body>
</html>
```